Landing-Page-Design für Immobilienunternehmen
Zielgruppe
Die Firma Kalmt Immobilien kauft jegliche Art von Immobilien im Osten von Hamburg. Die Zielgruppe sind Immobilienbesitzer, welche ihre Wohnung, Haus, Gewerbe oder Sonstiges verkaufen möchten/müssen.
Ich würde gerne drei Unterzielgruppe mehr ansprechen:
Verkauf weil geerbt
textlich untermauert
Verkauf weil ins Altersheim
Verkauf weil ein Geldengpass
Wir kaufen:
Häuser
Eigentumswohnungen
Gewerbeflächen
Mehrfamilienhäuser
Garagen
Agrarflächen (Wald, Acker, Wiese, Teiche)
Aufgabenstellung
Es besteht ein Logo, welches berücksichtigt werden müsste.
Außerdem:
- responsive
- seriös
- conversion optimiert
- viel bebildert, textliche untermauert
- vertrauensvoll/verschwiegen
Telefonnummer soll prominent dargestellt werden, genauso wie ein Kontaktformular.

```html
<!DOCTYPE html>
<html lang="de">
<head>
<meta charset="utf-8">
<title>Kalmt Immobilien – Wir kaufen Immobilien</title>
<link href="https://fonts.googleapis.com/css2?family=Roboto+Condensed:wght@300;400;700&family=Roboto:ital,wght@0,300;0,400;0,700;1,700&display=swap" rel="stylesheet">
<style>
:root{
  --green:#76b82a;
  --dark:#2f3035;
  --grey-bg:#f4f4f4;
  --card-bg:#f1f1f1;
  --text:#6b6b6b;
  --footer:#1d1d1f;
  --footer-bar:#0d0d0e;
  --button:#8c8c8c;
}
*{box-sizing:border-box;margin:0;padding:0}
html,body{width:1200px;height:2747px;overflow:hidden;background:#fff}
body{font-family:"Roboto",Arial,sans-serif;color:var(--text);position:relative}
.abs{position:absolute}

/* Header */
.brand{left:143px;top:234px;white-space:nowrap}
.brand-name{display:flex;align-items:center;gap:16px;font-family:"Roboto Condensed",Arial,sans-serif;font-weight:700;font-size:54px;line-height:1;letter-spacing:3px;color:var(--green)}
.brand-name .mark{width:42px;height:42px;background:var(--dark)}
.brand-tag{margin-top:14px;font-family:"Roboto Condensed",Arial,sans-serif;font-size:22px;line-height:1;letter-spacing:2.5px;color:var(--dark)}
.hero-banner{left:0;top:0;width:1200px;height:290px}
.hero-text{left:742px;top:42px;width:440px;text-align:center;transform:rotate(-7deg);transform-origin:center}
.hero-text .big{font-weight:700;font-size:34px;line-height:36px;color:#fff}
.hero-text .small{margin-top:12px;font-weight:700;font-size:24px;line-height:28px;color:var(--dark)}

/* Section headings */
.section-title{left:0;width:1200px;text-align:center;font-family:"Roboto Condensed",Arial,sans-serif;font-weight:300;font-size:35px;line-height:1.2;color:var(--green)}
.section-sub{left:0;width:1200px;text-align:center;font-family:"Roboto Condensed",Arial,sans-serif;font-size:24px;color:#555}

/* Reason cards */
.card{position:absolute;top:491px;width:338px;height:476px;background:var(--card-bg)}
.card-head{height:49px;background:var(--green);color:#fff;font-family:"Roboto Condensed",Arial,sans-serif;font-size:22px;letter-spacing:2px;text-align:center;line-height:49px;white-space:nowrap}
.card-photo{height:223px}
.card-text{padding:26px 64px 0 46px;font-family:"Roboto Condensed",Arial,sans-serif;font-weight:300;font-size:16.5px;line-height:20.5px;text-align:justify;color:#666}
.card-text .more{color:var(--green);margin-left:18px}

/* Call */
.call-shape{left:0;top:940px;width:520px;height:150px}
.call-text{left:295px;top:982px;width:160px;text-align:center;color:#fff;font-weight:700;font-size:25px;line-height:27px;transform:rotate(-6deg)}
.phone{left:501px;top:978px;font-weight:700;font-style:italic;font-size:40px;color:var(--green);letter-spacing:1px;white-space:nowrap}

/* Grey band */
.grey-band{left:0;top:1088px;width:1200px;height:945px;background:var(--grey-bg)}
.type{position:absolute;top:1135px;width:202px;text-align:center}
.type .type-photo{height:200px}
.type .type-name{margin-top:17px;font-family:"Roboto Condensed",Arial,sans-serif;font-size:20px;color:#333;white-space:nowrap}
.type .type-btn{display:inline-block;margin-top:6px;width:92px;height:26px;line-height:22px;background:var(--green);border:2px solid #dcdcdc;color:#fff;font-family:"Roboto Condensed",Arial,sans-serif;font-size:18px}
.arrow{top:1212px;width:26px;height:44px}

/* Contact */
.contact-shapes{left:0;top:1400px;width:1200px;height:650px}
.contact-title{left:120px;top:1505px;width:580px;text-align:center;color:#fff;font-weight:700;font-size:45px;line-height:43px;transform:rotate(-6deg)}
.field{position:absolute;height:44px;background:#fff;padding-left:25px;line-height:44px;font-weight:300;font-size:22px;color:#b5b5b5}
.submit{left:200px;top:1925px;width:341px;height:42px;border-radius:21px;background:var(--button);color:#fff;text-align:center;line-height:42px;font-size:18px}

/* Gallery */
.g{position:absolute}

/* Footer */
.footer{left:0;top:2562px;width:1200px;height:185px;background:var(--footer)}
.footer-brand{left:0;top:2668px;width:1365px;text-align:center}
.footer-brand .name{display:inline-flex;align-items:center;gap:8px;font-family:"Roboto Condensed",Arial,sans-serif;font-weight:700;font-size:22px;line-height:1;letter-spacing:1.5px;color:var(--green)}
.footer-brand .name .mark{width:16px;height:16px;background:#fff}
.footer-brand .tag{font-family:"Roboto Condensed",Arial,sans-serif;font-size:9px;letter-spacing:1.2px;color:#ddd;margin-top:3px}
.social{left:888px;top:2623px;display:flex;gap:14px}
.social span{width:16px;height:16px;border-radius:50%;background:#fff}
.footer-bar{left:0;top:2718px;width:1200px;height:29px;background:var(--footer-bar)}
.footer-links{left:573px;top:2724px;font-family:"Roboto Condensed",Arial,sans-serif;font-size:10.5px;letter-spacing:.6px;color:#e0e0e0;word-spacing:2px;white-space:nowrap}
</style>
</head>
<body>

<svg class="abs hero-banner" viewBox="0 0 1200 290" aria-hidden="true">
  <polygon points="723,45 1200,0 1200,190 1182,193 868,225 869,280 741,237" fill="var(--green)"/>
</svg>
<div class="abs hero-text">
  <div class="big">Wir kaufen Immobilien<br>jeglicher Art<br>im Osten von Hamburg!</div>
  <div class="small">Diskret, vertraulich,<br>unbürokratisch &amp; schnell.</div>
</div>

<div class="abs brand">
  <div class="brand-name"><span class="mark"></span>KALMT IMMOBILIEN</div>
  <div class="brand-tag">VERWALTUNG · BERATUNG · INVESTMENT</div>
</div>

<h2 class="abs section-title" style="top:390px">BEI UNS IST IHRE IMMOBILIE IN GUTER HAND</h2>
<p class="abs section-sub" style="top:436px">Egal, warum Sie verkaufen wollen!</p>

<div class="card" style="left:68px">
  <div class="card-head">SIE HABEN GEERBT?</div>
  <div class="card-photo" role="img" aria-label="Ältere Hände halten ein kleines Holzhaus" style="background:linear-gradient(135deg,#c9c9c9,#a9a9a9)"></div>
  <p class="card-text">At vero eos et accusam et justo duo dolores et ea rebum. Stet clita kasd gubergren, no sea taki-mata sanctus est Lorem ipsum dolor sit amet. Lorem ipsum dolor sit amet, consetetur sadipscing elitr, sed diam nonu<span class="more">MEHR</span></p>
</div>
<div class="card" style="left:431px">
  <div class="card-head">SIE GEHEN INS ALTERSHEIM?</div>
  <div class="card-photo" role="img" aria-label="Nahaufnahme einer älteren Person" style="background:linear-gradient(90deg,#f4f4f4,#e6dcd6 60%,#b8a79c)"></div>
  <p class="card-text">At vero eos et accusam et justo duo dolores et ea rebum. Stet clita kasd gubergren, no sea taki-mata sanctus est Lorem ipsum dolor sit amet. Lorem ipsum dolor sit amet, consetetur sadipscing elitr, sed diam nonu<span class="more">MEHR</span></p>
</div>
<div class="card" style="left:800px">
  <div class="card-head">SIE HABEN GELDENGPASS?</div>
  <div class="card-photo" role="img" aria-label="Leere Hosentasche als Zeichen für Geldnot" style="background:linear-gradient(90deg,#3a3a36,#6e6b62 60%,#eaeaea)"></div>
  <p class="card-text">At vero eos et accusam et justo duo dolores et ea rebum. Stet clita kasd gubergren, no sea taki-mata sanctus est Lorem ipsum dolor sit amet. Lorem ipsum dolor sit amet, consetetur sadipscing elitr, sed diam nonu<span class="more">MEHR</span></p>
</div>

<div class="abs grey-band"></div>
<svg class="abs call-shape" viewBox="0 940 520 150" aria-hidden="true">
  <polygon points="256,976 491,952 481,1040 330,1055 326,1078 262,1058" fill="var(--green)"/>
</svg>
<div class="abs call-text">Rufen Sie<br>uns an!</div>
<div class="abs phone">+49 4100 5550123</div>

<svg class="abs arrow" style="left:20px" viewBox="0 0 26 44" aria-hidden="true"><polyline points="22,2 3,22 22,42" fill="none" stroke="#555" stroke-width="2"/></svg>
<svg class="abs arrow" style="left:1152px" viewBox="0 0 26 44" aria-hidden="true"><polyline points="4,2 23,22 4,42" fill="none" stroke="#555" stroke-width="2"/></svg>

<div class="type" style="left:74px">
  <div class="type-photo" role="img" aria-label="Einfamilienhaus mit rotem Dach" style="background:linear-gradient(180deg,#cfd9e0,#e8e4de 50%,#6d7a4a)"></div>
  <div class="type-name">Häuser</div><span class="type-btn">MEHR</span>
</div>
<div class="type" style="left:291px">
  <div class="type-photo" role="img" aria-label="Helle leere Eigentumswohnung mit Küche" style="background:linear-gradient(135deg,#f6f6f6,#d9d9d9)"></div>
  <div class="type-name">Eigentumswohnungen</div><span class="type-btn">MEHR</span>
</div>
<div class="type" style="left:511px">
  <div class="type-photo" role="img" aria-label="Luftbild eines Gewerbegebiets" style="background:linear-gradient(135deg,#8aa06a,#9ea5a8 50%,#6f8a4e)"></div>
  <div class="type-name">Gewerbeflächen</div><span class="type-btn">MEHR</span>
</div>
<div class="type" style="left:727px">
  <div class="type-photo" role="img" aria-label="Weißes Altbau-Mehrfamilienhaus" style="background:linear-gradient(180deg,#b9cde6,#e9e9e6 40%,#cfcfca)"></div>
  <div class="type-name">Mehrfamilienhäuser</div><span class="type-btn">MEHR</span>
</div>
<div class="type" style="left:941px">
  <div class="type-photo" role="img" aria-label="Blaue Garage mit weißen Toren" style="background:linear-gradient(180deg,#9cc0e4,#4b6f96 50%,#e6e6e6)"></div>
  <div class="type-name">Garagen</div><span class="type-btn">MEHR</span>
</div>

<svg class="abs contact-shapes" viewBox="0 1400 1200 650" aria-hidden="true">
  <defs>
    <linearGradient id="houseTones" x1="0" y1="0" x2="0" y2="1">
      <stop offset="0" stop-color="#dfe7ee"/>
      <stop offset=".45" stop-color="#e7e3df"/>
      <stop offset=".8" stop-color="#9a8f7a"/>
      <stop offset="1" stop-color="#6a4f78"/>
    </linearGradient>
  </defs>
  <path d="M0,1533 L832,1447 L766,1950 Q700,2000 560,2012 L0,2043 Z" fill="var(--green)"/>
  <path d="M832,1447 L1200,1410 L1200,1935 L766,1952 Z" fill="url(#houseTones)" role="img" aria-label="Weißes Landhaus mit rotem Dach und Blumengarten"/>
</svg>
<h2 class="abs contact-title">Nehmen Sie unverbindlich<br>und vertrauensvoll<br>Kontakt mit uns auf!</h2>
<div class="field" style="left:146px;top:1735px;width:487px">Vollständiger Name</div>
<div class="field" style="left:146px;top:1789px;width:487px">Art der Immobilie</div>
<div class="field" style="left:146px;top:1844px;width:209px">e-mail</div>
<div class="field" style="left:424px;top:1844px;width:209px">Telefon</div>
<div class="abs submit">Unverbindliches Angebot anfordern!</div>

<h2 class="abs section-title" style="top:2049px">BEI UNS IST IHRE IMMOBILIE IN GUTER HAND</h2>
<p class="abs section-sub" style="top:2095px">Egal, warum Sie verkaufen wollen!</p>

<div class="g" role="img" aria-label="Helle Dachgeschosswohnung" style="left:28px;top:2149px;width:183px;height:182px;background:linear-gradient(135deg,#eeeeee,#a9a39a)"></div>
<div class="g" role="img" aria-label="Grundstücksplan mit markierter Parzelle" style="left:221px;top:2141px;width:183px;height:183px;background:linear-gradient(135deg,#f2f2f2,#d4d4d4)"></div>
<div class="g" role="img" aria-label="Weiße Stadtvilla" style="left:411px;top:2141px;width:186px;height:185px;background:linear-gradient(180deg,#f3f3f3,#e2e2e0 55%,#6f8b55)"></div>
<div class="g" role="img" aria-label="Wald von oben" style="left:603px;top:2147px;width:376px;height:376px;background:linear-gradient(135deg,#5e8a4c,#2f5a2f 60%,#4d7a3f)"></div>
<div class="g" role="img" aria-label="Gepflügter Acker" style="left:988px;top:2147px;width:184px;height:183px;background:linear-gradient(180deg,#cfe0ea,#8aa259 30%,#7a5a40 45%,#5e4330)"></div>
<div class="g" role="img" aria-label="Luftbild einer Gewerbeimmobilie" style="left:30px;top:2343px;width:181px;height:183px;background:linear-gradient(135deg,#7aa05a,#9aa3a7 50%,#6c9150)"></div>
<div class="g" role="img" aria-label="Modernes Mehrfamilienhaus" style="left:220px;top:2343px;width:184px;height:183px;background:linear-gradient(180deg,#8fb8e3,#e7e7e4 45%,#bfbfbb)"></div>
<div class="g" role="img" aria-label="Teich mit Seerosen" style="left:412px;top:2342px;width:186px;height:185px;background:linear-gradient(180deg,#d8dde0,#7d9b55 45%,#3f5a3a)"></div>
<div class="g" role="img" aria-label="Moderne Reihenhäuser" style="left:987px;top:2343px;width:186px;height:186px;background:linear-gradient(180deg,#e6eaed,#d8d8d6 50%,#7d9168)"></div>

<footer>
  <div class="abs footer"></div>
  <div class="abs footer-brand">
    <div class="name"><span class="mark"></span>KALMT IMMOBILIEN</div>
    <div class="tag">VERWALTUNG · BERATUNG · INVESTMENT</div>
  </div>
  <div class="abs social" aria-hidden="true"><span></span><span></span><span></span><span></span></div>
  <div class="abs footer-bar"></div>
  <nav class="abs footer-links">KONTAKT | AGB | WIDERRUFSRECHT | ZAHLUNGSINFORMATION | DATENSCHUTZ | IMPRESSUM</nav>
</footer>

</body>
</html>
```